Letterhead for Conveyancing Company

Use existing logo to create a letterhead for a conveyancing company. Must be able to be used in Microsoft Word. Easy to read and professional.
Contact information to be at the bottom.
Bright Oak Conveyancing Pty Ltd
ACN 621 984 736PO Box 535 Campbelltown SA 5074
Mobile - 0461739286
Web address - www.brightoakconveyancing.com.au

Requirements
Must have
• Logo and contact details.
• Simple and professional.

```html
<!DOCTYPE html>
<html lang="en">
<head>
<meta charset="utf-8">
<title>Bright Oak Conveyancing – Letterhead</title>
<link href="https://fonts.googleapis.com/css2?family=Didact+Gothic&family=Roboto:wght@400;700;900&display=swap" rel="stylesheet">
<style>
  :root {
    --backdrop: #e4e4e4;
    --paper: #f4f4f4;
    --brand-pink: #e6449a;
    --brand-grey: #7b7b7b;
    --accent-bar: #8a8a8a;
    --body-text: #5a5a5a;
    --heading-text: #4a4a4a;
    --ink-blue: #3d63b0;
  }
  * { margin: 0; padding: 0; box-sizing: border-box; }
  html, body { width: 1024px; height: 1200px; overflow: hidden; }
  body { background: var(--backdrop); font-family: "Didact Gothic", sans-serif; }

  .letterhead {
    position: absolute; left: 111px; top: 40px;
    width: 802px; height: 1120px;
    background: var(--paper);
    box-shadow: 0 2px 10px rgba(0,0,0,0.12);
  }
  .side-bar {
    position: absolute; left: 0; top: 70px;
    width: 12px; height: 108px;
    background: var(--accent-bar);
  }
  .brand-name {
    position: absolute; left: 56px; top: 86px;
    font-family: "Roboto", sans-serif; font-weight: 900;
    font-size: 44px; line-height: 1; letter-spacing: -1px;
    color: var(--brand-grey);
  }
  .contact-panel {
    position: absolute; left: 524px; top: 71px;
    width: 278px; height: 107px;
    background: var(--brand-pink); color: #fff;
    font-family: "Roboto", sans-serif; font-size: 12.5px; line-height: 16.5px;
    text-align: right; padding: 8px 16px 0 10px;
  }
  .contact-panel .company { font-weight: 700; }
  .contact-panel .gap { height: 5px; }
  .contact-line { display: flex; justify-content: flex-end; align-items: center; gap: 8px; }
  .contact-line svg { width: 11px; height: 11px; flex: none; }

  .salutation {
    position: absolute; left: 77px; top: 296px;
    font-size: 19px; color: var(--heading-text);
  }
  .letter-body {
    position: absolute; left: 77px; top: 351px; width: 657px;
    font-size: 11.4px; line-height: 15px; color: var(--body-text);
    text-align: justify; hyphens: auto;
  }
  .letter-body p { margin-bottom: 15px; }
  .sign-off {
    position: absolute; left: 77px; top: 710px;
    font-size: 11.4px; color: var(--body-text);
  }
  .signature {
    position: absolute; left: 77px; top: 776px;
    width: 136px; height: 66px;
    background: linear-gradient(90deg, rgba(61,99,176,0.18), rgba(61,99,176,0.08));
    border-radius: 4px;
  }
</style>
</head>
<body>
  <main class="letterhead">
    <div class="side-bar"></div>
    <div class="brand-name">Bright Oak</div>

    <address class="contact-panel" style="font-style:normal">
      <div class="company">Bright Oak Conveyancing Pty Ltd</div>
      <div>PO Box 871 Marlowdale SA 5096</div>
      <div>ACN 583 217 469</div>
      <div class="gap"></div>
      <div class="contact-line">0461739286
        <svg viewBox="0 0 24 24" aria-hidden="true"><path fill="#fff" d="M6.6 10.8a15.1 15.1 0 0 0 6.6 6.6l2.2-2.2a1 1 0 0 1 1-.25 11.4 11.4 0 0 0 3.6.57 1 1 0 0 1 1 1V20a1 1 0 0 1-1 1A17 17 0 0 1 3 4a1 1 0 0 1 1-1h3.5a1 1 0 0 1 1 1c0 1.25.2 2.45.57 3.57a1 1 0 0 1-.25 1z"/></svg>
      </div>
      <div class="contact-line">www.brightoakconveyancing.com.au
        <svg viewBox="0 0 24 24" aria-hidden="true"><circle cx="12" cy="12" r="10" fill="#fff"/><path d="M12 2c-3 3-3 17 0 20M2 12h20M4 7h16M4 17h16" stroke="#e6449a" stroke-width="1.6" fill="none"/></svg>
      </div>
    </address>

    <h1 class="salutation" style="font-weight:400">Dear Mr. Hartley,</h1>

    <section class="letter-body">
      <p>Lorem ipsum dolor sit amet, consectetur adipiscing elit. Donec orci purus, luctus vitae dignissim eu, iaculis sed purus. Vivamus faucibus, ipsum nec aliquet viverra, leo mauris condimentum ligula, sit amet sagittis enim ligula quis arcu. Nam egestas tortor id nisi porttitor mattis. In tortor ante, ultricies in suscipit a, tempus non massa. Vivamus et auctor mi. Fusce vel massa nulla. Phasellus nec eros mauris, et scelerisque orci.</p>
      <p>Donec malesuada orci vitae nulla accumsan porta a id massa. Quisque accumsan iaculis magna sit amet fringilla. Maecenas consequat, magna eget tincidunt semper, odio nibh rutrum mi, id feugiat ante nisi eu risus. Vestibulum nunc orci, rhoncus a placerat in, ultricies in mi. Cras mattis varius eros, vel fringilla nisi suscipit eget. Quisque scelerisque sagittis nulla at porttitor.</p>
      <p>Sed id augue vitae urna euismod commodo aliquet a quam. Pellentesque arcu velit, cursus et malesuada ut, consequat et diam. Nullam erat sem, rhoncus id ullamcorper vitae, rhoncus et arcu. In ultricies ultricies nulla, ut rutrum nisi iaculis at. Donec eu magna a metus ornare faucibus. Fusce aliquet faucibus ultricies. Morbi semper, est id tincidunt gravida, sem arcu adipiscing lacus, ac bibendum nulla leo eu purus. Quisque nec diam sed risus consectetur a ccumsan quis quis nibh. Vestibulum id purus lorem.</p>
      <p>It is a long established fact that a reader will be distracted by the readable content of a page when looking at its layout. The point of using Lorem Ipsum is that it has a more-or-less normal distribution of letters, as opposed to using 'Content here, content here', making it look like readable English. Many desktop publishing packages</p>
    </section>

    <div class="sign-off">Sincerely,</div>
    <div class="signature" role="img" aria-label="Handwritten signature of James Hartley in blue ink"></div>
  </main>
</body>
</html>
```